Harbor Crestline (Business Card Design)

Need business cards designed. Something modern, chic, and sleek. Mabye the back of the card should be the navy blue that is in the logo and then just the logo on the back.

Target Market(s)

Those in the hotel, office, and renovation industry

Contact Information for Business Card

1. Logo 2. Dorian Fenwick 3. CEO/Founder 4. Phone: (833) HarbCre / (833) 427-2731 5. Email: dorian@theharborcrestline.com 6. Website: www.theharborcrestline.com

Font styles to use
Other font styles liked:
• Look at the logo font and base the font for everything else off of that.

Colors
0054AA
0677BA
7BADD7
CADEEF
E8F1F8

Requirements
Must have
• Colors that are associated in the logo
Nice to have
• Sleek modern clean and chic design.

```html
<!DOCTYPE html>
<html lang="en">
<head>
<meta charset="utf-8">
<title>Harbor Crestline – Business Card</title>
<link href="https://fonts.googleapis.com/css2?family=Montserrat:wght@600;700&family=Open+Sans:wght@400&display=swap" rel="stylesheet">
<style>
  :root {
    --navy: #0c1a44;
    --navy-light: #1c3a8f;
    --gold: #d2a447;
    --white: #ffffff;
    --backdrop: #1e1e1e;
  }
  * { margin: 0; padding: 0; box-sizing: border-box; }
  html, body { width: 1200px; height: 1015px; overflow: hidden; }
  body {
    background: var(--backdrop);
    position: relative;
    font-family: "Open Sans", sans-serif;
  }
  .card {
    position: absolute;
    left: 250px;
    width: 700px;
    height: 400px;
    background: var(--navy);
    overflow: hidden;
  }
  .card--back { top: 60px; }
  .card--front { top: 545px; }

  .brand {
    position: absolute;
    display: flex;
    align-items: center;
    gap: 12px;
    font-family: "Montserrat", sans-serif;
    font-weight: 700;
    text-transform: uppercase;
    letter-spacing: 0.06em;
    white-space: nowrap;
  }
  .brand__mark { width: 14px; height: 14px; background: var(--gold); flex: none; }
  .brand__name { display: block; line-height: 1.15; }
  .card--back .brand {
    left: 50%; top: 50%;
    transform: translate(-50%, -50%);
    font-size: 40px;
    color: var(--navy-light);
  }
  .card--front .brand {
    left: 462px; top: 96px;
    width: 226px;
    justify-content: center;
    gap: 10px;
    font-size: 24px;
    color: var(--navy);
  }
  .card--front .brand__mark { width: 11px; height: 11px; }

  .front-art { position: absolute; inset: 0; }

  .contact {
    position: absolute;
    left: 42px; top: 40px;
    list-style: none;
    color: var(--white);
    font-size: 15px;
    line-height: 1;
  }
  .contact__item { display: flex; align-items: center; gap: 10px; margin-bottom: 12px; }
  .contact__icon { width: 16px; height: 16px; flex: none; }

  .person {
    position: absolute;
    left: 42px; bottom: 38px;
  }
  .person__name {
    font-family: "Montserrat", sans-serif;
    font-weight: 700;
    font-size: 28px;
    color: var(--white);
    text-transform: uppercase;
    letter-spacing: 0.01em;
  }
  .person__title {
    font-size: 17px;
    color: var(--gold);
    text-transform: uppercase;
    margin-top: 2px;
  }
</style>
</head>
<body>

  <section class="card card--back" aria-label="Card back">
    <div class="brand"><span class="brand__mark"></span><span class="brand__name">Harbor Crestline</span></div>
  </section>

  <section class="card card--front" aria-label="Card front">
    <svg class="front-art" width="700" height="400" viewBox="0 0 700 400" aria-hidden="true">
      <polygon points="425,0 700,0 700,300 408,262" fill="var(--white)"/>
      <polyline points="450,18 432,244 700,282" fill="none" stroke="var(--navy)" stroke-width="5"/>
      <rect x="446" y="2" width="8" height="7" fill="var(--gold)"/>
    </svg>

    <div class="brand"><span class="brand__mark"></span><span class="brand__name">Harbor<br>Crestline</span></div>

    <ul class="contact">
      <li class="contact__item">
        <svg class="contact__icon" viewBox="0 0 24 24"><path fill="var(--gold)" d="M6.6 10.8a15 15 0 0 0 6.6 6.6l2.2-2.2a1 1 0 0 1 1-.25 11.4 11.4 0 0 0 3.6.57 1 1 0 0 1 1 1V20a1 1 0 0 1-1 1A17 17 0 0 1 3 4a1 1 0 0 1 1-1h3.5a1 1 0 0 1 1 1c0 1.250.2 2.450.57 3.570a1 1 0 0 1-.25 1z"/></svg>
        (833) HarbCre / (833) 427-2731
      </li>
      <li class="contact__item">
        <svg class="contact__icon" viewBox="0 0 24 24"><rect x="2" y="5" width="20" height="14" fill="var(--gold)"/><path d="M2 5l10 8 10-8" fill="none" stroke="var(--navy)" stroke-width="1.6"/></svg>
        dorian@theharborcrestline.com
      </li>
      <li class="contact__item">
        <svg class="contact__icon" viewBox="0 0 24 24" fill="none" stroke="var(--gold)" stroke-width="2"><circle cx="12" cy="12" r="10"/><ellipse cx="12" cy="12" rx="4.5" ry="10"/><path d="M2 12h20M4 7h16M4 17h16"/></svg>
        www.theharborcrestline.com
      </li>
    </ul>

    <div class="person">
      <div class="person__name">Dorian Fenwick</div>
      <div class="person__title">CEO/Founder</div>
    </div>
  </section>

</body>
</html>
```